I would like some help creating my first business cards for my new business, I am a facilitator of a course that I have created. I am currently starting the sales promotion and marketing part of my business and need some help designing the business cards. Something fairly simple would be good, the core theme of my work is in connection of women to themselves and to each other. My initial design is a tree lit up by lights, a very mother earth type of image. This is not my design however so I probably am not legally able to use the design. I don't have a logo. Could you possibly assist with this?

I would really like to have the following details on the business card:
Meg Donlan
0431 582 917
hi.meg.donlan@larkmail.example

And also the image

Target Market(s)

Women who are living in an isolated environment

Industry/Entity Type

Counsellor

Contact Information for Business Card

Meg Donlan
Facilitator
hi.meg.donlan@larkmail.example
0431 582 917

Font styles to use
Other font styles liked:
• Handwriting - Dakota

Colors
e34197
fee18a
3276b5
33a6d7
33b8a4

Requirements
Must have
• 1) My details as above
• 2) a design (picture) that represents the mother earth theme similar to the designs included in the brief
• 3) no copyright attached to the design
• 4) Colours are very important but it is difficult to describe the colour using the colour wheel. Please refer to the example of the tree that I have included in the drop box.
• 5) I must apologise that I forgot to add the business card needs to have the name of the business in gold letters please: Riverbend Circle Gatherings Collective, thank you
Nice to have
• It would be great to use the tree design that I included in the brief, this is my favourite picture but I think it is probably copyrighted. If it's not, that is the one I would like on my business cards please.

```html
<!DOCTYPE html>
<html lang="en">
<head>
<meta charset="utf-8">
<title>Meg Donlan – Business Card</title>
<link rel="stylesheet" href="https://fonts.googleapis.com/css2?family=Open+Sans:wght@400;700&family=Parisienne&display=swap">
<style>
  :root {
    --page-bg: #e9ecdf;
    --card-light: #fffef3;
    --card-cream: #fbf8cf;
    --earth-brown: #5e4424;
    --name-brown: #4a3a24;
    --muted-grey: #6d6a60;
    --gold-deep: #ee8a1a;
    --gold-light: #f5b51c;
    --tree-orange: #f7b64a;
    --tree-peach: #f3c98a;
    --tree-teal: #bfdcc8;
  }
  * { box-sizing: border-box; margin: 0; padding: 0; }
  html, body {
    width: 1200px; height: 898px; overflow: hidden;
    background: var(--page-bg);
  }
  .business-card {
    position: absolute; left: 100px; top: 163px;
    width: 1000px; height: 572px; overflow: hidden;
    background: radial-gradient(ellipse at 62% 45%, var(--card-light) 0%, var(--card-cream) 75%);
    box-shadow: 0 8px 24px rgba(60, 50, 20, 0.18);
    font-family: "Open Sans", sans-serif;
  }
  .contact-name {
    position: absolute; right: 60px; top: 34px; text-align: right;
  }
  .contact-name__name {
    font-size: 30px; font-weight: 700; color: var(--name-brown); line-height: 1.05;
  }
  .contact-name__role {
    font-size: 19px; color: var(--muted-grey); line-height: 1.1;
  }
  .business-name {
    position: absolute; left: 500px; top: 120px; width: 470px;
    font-family: "Parisienne", cursive; font-size: 56px; font-weight: 400; line-height: 68px;
    color: var(--gold-deep);
  }
  .business-name span { display: block; white-space: nowrap; }
  .business-name span:nth-child(2) { padding-left: 40px; }
  .business-name span:nth-child(3) { padding-left: 80px; color: var(--gold-light); }
  .tree-art {
    position: absolute; left: 30px; top: 150px; width: 370px; height: 370px;
    background: radial-gradient(closest-side at 50% 45%,
      var(--tree-orange) 0%, var(--tree-peach) 40%, var(--tree-teal) 70%, rgba(251, 248, 207, 0) 100%);
  }
  .ground {
    position: absolute; left: 0; bottom: 0; width: 1000px; height: 150px;
  }
  .contact-details {
    position: absolute; right: 40px; top: 398px;
    display: flex; gap: 26px; align-items: center;
    font-size: 19px; color: var(--name-brown); white-space: nowrap;
  }
  .contact-details__item { display: flex; align-items: center; gap: 9px; }
  .contact-details__icon { width: 22px; height: 22px; flex: none; }
</style>
</head>
<body>
  <main class="business-card">
    <div class="contact-name">
      <div class="contact-name__name">Meg Donlan</div>
      <div class="contact-name__role">Facilitator</div>
    </div>

    <h1 class="business-name">
      <span>Riverbend Circle</span>
      <span>Gatherings</span>
      <span>Collective</span>
    </h1>

    <div class="tree-art" role="img" aria-label="Illustration of a tree with swirling coloured rings and star-like blossoms in its crown"></div>

    <svg class="ground" viewBox="0 0 1000 150" preserveAspectRatio="none" aria-hidden="true">
      <path d="M0 118 C 250 110, 520 90, 760 62 C 860 50, 940 44, 1000 40 L1000 150 L0 150 Z" fill="var(--earth-brown)"/>
    </svg>

    <div class="contact-details">
      <div class="contact-details__item">
        <svg class="contact-details__icon" viewBox="0 0 24 24" aria-hidden="true">
          <circle cx="12" cy="12" r="11" fill="none" stroke="var(--name-brown)" stroke-width="1.6"/>
          <path d="M6.5 10.5c0-2 2.5-3 5.5-3s5.5 1 5.5 3l-1.8.4-.7-1.4h-6l-.7 1.4z M8.5 12h7l1.5 4.5h-10z" fill="var(--name-brown)"/>
        </svg>
        <span>0431 582 917</span>
      </div>
      <div class="contact-details__item">
        <svg class="contact-details__icon" viewBox="0 0 24 24" aria-hidden="true">
          <circle cx="12" cy="12" r="11" fill="none" stroke="var(--name-brown)" stroke-width="1.6"/>
          <rect x="6" y="8" width="12" height="8.5" rx="1" fill="none" stroke="var(--name-brown)" stroke-width="1.5"/>
          <path d="M6.5 8.5l5.5 4.5 5.5-4.5" fill="none" stroke="var(--name-brown)" stroke-width="1.5"/>
        </svg>
        <span>hi.meg.donlan@larkmail.example</span>
      </div>
    </div>
  </main>
</body>
</html>
```